New business blog needs wordpress theme

I need a unique wordpress theme for my new business oriented blog at hollowpeakdesk.com. The blog focuses on my experience as an entrepreneur and offers insights into business problems while chronicling my experience building a new company.

I would like to see a theme that looks more like a creative professional's website, not a business website. Large photos, bright colors, unique layout. I do not want stock photos of people in suits doing business type things. Also, no pictures of me - I am blogging anonymously.

The design should communicate technology and beauty - for example, I really like the feel of the landing page at www.tundrelo.com - it is beautiful to look at but also reflects the cutting edge nature of what they are doing.

Industry/Entity Type

Business

```html
<!DOCTYPE html>
<html lang="en">
<head>
<meta charset="utf-8">
<title>Hollow Peak Desk</title>
<link rel="stylesheet" href="https://fonts.googleapis.com/css2?family=Open+Sans:wght@300;400;600;700&display=swap">
<style>
:root{
  --navy:#0d1724;
  --hero-top:#16222f;
  --hero-bottom:#3b4d5c;
  --blue:#2a6fc4;
  --blue-dark:#1b4f93;
  --footer:#1f5aa6;
  --footer-bar:#174785;
  --text:#555b62;
  --muted:#8a9098;
  --line:#e3e6ea;
  --pill:#eef0f3;
  --white:#ffffff;
}
*{box-sizing:border-box;margin:0;padding:0}
html,body{width:828px;height:1200px;overflow:hidden}
body{font-family:"Open Sans",Arial,sans-serif;background:var(--white);color:var(--text);position:relative}
.hero{position:absolute;left:0;top:0;width:828px;height:362px;background:linear-gradient(180deg,var(--hero-top) 0%,#24323f 55%,var(--hero-bottom) 100%)}
.hero-photo{position:absolute;inset:0;background:radial-gradient(ellipse at 62% 38%,rgba(120,150,170,.35),transparent 60%)}
.topbar{position:absolute;left:0;top:0;width:828px;height:58px;background:rgba(8,14,22,.75);display:flex;align-items:center;padding:0 40px}
.brand{color:var(--white)}
.brand-name{font-size:19px;font-weight:700;line-height:1.1}
.brand-tag{font-size:7px;color:#aeb7c1;width:190px;line-height:1.3;margin-top:2px}
.nav{margin-left:auto;display:flex;gap:22px;font-size:8.5px;color:#cfd6de;align-items:center}
.search{width:90px;height:17px;background:#2a3542;border-radius:2px;margin-left:8px}
.arrow{position:absolute;top:190px;width:18px;height:28px}
.hero-text{position:absolute;left:0;width:828px;text-align:center;color:var(--white)}
.hero-title{top:222px;font-size:36px;font-weight:300}
.hero-sub{top:272px;font-size:17px;font-weight:300;line-height:1.45}
.hero-btn{position:absolute;left:343px;top:335px;width:146px;height:28px;border:1px solid rgba(255,255,255,.8);background:rgba(0,0,0,.35);color:var(--white);font-size:12px;display:flex;align-items:center;justify-content:center}
.blog{position:absolute;left:44px;top:382px;width:478px}
.section-label{font-size:9px;font-weight:700;color:var(--blue);letter-spacing:.4px}
.intro{font-size:7.5px;line-height:1.5;margin-top:6px}
.post{margin-top:18px}
.post-title{font-size:13px;font-weight:600;color:var(--blue);background:#f4f6f8;padding:5px 8px;border-bottom:1px solid var(--line)}
.post-body{display:flex;gap:14px;margin-top:12px}
.post-image{width:150px;height:96px;flex:none}
.post-copy{font-size:7.5px;line-height:1.55}
.meta{display:flex;gap:6px;margin-top:8px}
.pill{background:var(--pill);font-size:6.5px;color:var(--muted);padding:3px 8px;border-radius:2px}
.pager{position:absolute;left:180px;top:1070px;display:flex;gap:4px}
.pager span{border:1px solid #cfd4da;font-size:8px;padding:3px 7px;color:var(--text)}
.sidebar{position:absolute;left:546px;top:382px;width:244px}
.recent{margin-top:8px}
.recent-item{display:flex;gap:8px;margin-bottom:10px}
.thumb{width:42px;height:32px;flex:none}
.recent-title{font-size:7.5px;color:var(--blue);line-height:1.4}
.learn{display:block;margin-left:auto;width:58px;height:14px;background:var(--blue-dark);color:var(--white);font-size:6.5px;text-align:center;line-height:14px;margin-bottom:18px}
.top-list{margin-top:8px}
.top-item{border-bottom:1px solid var(--line);padding:7px 0}
.top-item .t{font-size:7.5px;color:var(--blue)}
.top-item .d{font-size:6.5px;color:var(--muted);margin-top:2px}
.footer{position:absolute;left:0;top:1098px;width:828px;height:78px;background:var(--footer);color:var(--white);display:flex;gap:40px;padding:10px 44px}
.footer h4{font-size:8.5px;font-weight:600;margin-bottom:4px}
.footer p,.footer li{font-size:6.5px;line-height:1.5;color:#d6e2f2;list-style:none}
.f-about{width:210px}.f-links{width:110px}
.social{display:grid;grid-template-columns:repeat(3,auto);gap:4px 18px;margin-top:4px}
.social span{display:flex;align-items:center;gap:5px;font-size:6.5px;color:#d6e2f2}
.social i{width:11px;height:11px;border-radius:50%;background:#d6e2f2;display:inline-block}
.copyright{position:absolute;left:0;top:1176px;width:828px;height:24px;background:var(--footer-bar);color:#c7d6ea;font-size:6.5px;text-align:center;line-height:24px}
.to-top{position:absolute;right:44px;top:6px;width:12px;height:12px;background:#2f6cbc}
</style>
</head>
<body>
<header class="hero">
  <div class="hero-photo" role="img" aria-label="Night photograph of a lit suspension bridge over water"></div>
  <div class="topbar">
    <div class="brand">
      <div class="brand-name">Hollow Peak Desk</div>
      <div class="brand-tag">Rowan talks business, best practices and tips about small business growth</div>
    </div>
    <nav class="nav"><span>Small Business</span><span>Technology</span><span>About Rowan</span><span>Contact</span><span class="search"></span></nav>
  </div>
  <svg class="arrow" style="left:20px" viewBox="0 0 18 28"><path d="M14 2 L4 14 L14 26" stroke="#9aa6b2" stroke-width="2" fill="none"/></svg>
  <svg class="arrow" style="right:20px" viewBox="0 0 18 28"><path d="M4 2 L14 14 L4 26" stroke="#9aa6b2" stroke-width="2" fill="none"/></svg>
  <h1 class="hero-text hero-title" style="position:absolute">Hollow Peak Desk</h1>
  <p class="hero-text hero-sub" style="position:absolute">Rowan talks business. Best practices, articles and tips and<br>about small business in the United States.</p>
  <div class="hero-btn">Click here for Login</div>
</header>

<main class="blog">
  <div class="section-label">BLOG</div>
  <p class="intro">I decided to compare the results of a Dealwave campaign I completed with the cost of the equivalent campaigns. The revenue generated, the customers acquired and customer retention compared.</p>

  <article class="post">
    <h2 class="post-title">Comparing Direct Mail to Dealwave – By the Numbers</h2>
    <div class="post-body">
      <div class="post-image" role="img" aria-label="Green road sign against a blue sky" style="background:linear-gradient(135deg,#6fa6d8,#3f8a4a)"></div>
      <div class="post-copy">Unhappy with the results of a direct mail small scale campaign, I decided to compare the results to a Dealwave campaign I completed with the cost of the equivalent campaigns. The revenue generated, the customers acquired and customer retention compared, the revenue generated, the customers...
        <div class="meta"><span class="pill">March 4, 2013</span><span class="pill">In Marketing</span><span class="pill">3 comments</span></div>
      </div>
    </div>
  </article>

  <article class="post">
    <h2 class="post-title">Comparing Direct Mail to Dealwave – By the Numbers</h2>
    <div class="post-body">
      <div class="post-image" role="img" aria-label="City skyline at night with lights" style="background:linear-gradient(135deg,#1a2436,#4a5f80)"></div>
      <div class="post-copy">Unhappy with the results of a direct mail small scale campaign, I decided to compare the results to a Dealwave campaign I completed with the cost of the equivalent campaigns. The revenue generated, the customers acquired and customer retention compared, the revenue generated, the customers...
        <div class="meta"><span class="pill">March 4, 2013</span><span class="pill">In Marketing</span><span class="pill">3 comments</span></div>
      </div>
    </div>
  </article>

  <article class="post">
    <h2 class="post-title">Comparing Direct Mail to Dealwave – By the Numbers</h2>
    <div class="post-body">
      <div class="post-image" role="img" aria-label="Puzzle pieces on a grassy field under blue sky" style="background:linear-gradient(135deg,#5aa0e0,#7cc25a)"></div>
      <div class="post-copy">Unhappy with the results of a direct mail small scale campaign, I decided to compare the results to a Dealwave campaign I completed with the cost of the equivalent campaigns. The revenue generated, the customers acquired and customer retention compared, the revenue generated, the customers...
        <div class="meta"><span class="pill">March 4, 2013</span><span class="pill">In Marketing</span><span class="pill">3 comments</span></div>
      </div>
    </div>
  </article>
</main>

<nav class="pager"><span>Prev</span><span>1</span><span>2</span><span>3</span><span>4</span><span>5</span><span>6</span><span>…</span><span>22</span><span>Next</span></nav>

<aside class="sidebar">
  <div class="section-label">RECENT POSTS</div>
  <div class="recent">
    <div class="recent-item"><div class="thumb" role="img" aria-label="Road sign photo" style="background:linear-gradient(135deg,#6fa6d8,#3f8a4a)"></div><div class="recent-title">Comparing Direct Mail to Dealwave – By the Numbers</div></div>
    <div class="recent-item"><div class="thumb" role="img" aria-label="Night city photo" style="background:linear-gradient(135deg,#1a2436,#4a5f80)"></div><div class="recent-title">Comparing Direct Mail to Dealwave – By the Numbers</div></div>
    <div class="recent-item"><div class="thumb" role="img" aria-label="Puzzle pieces photo" style="background:linear-gradient(135deg,#5aa0e0,#7cc25a)"></div><div class="recent-title">Comparing Direct Mail to Dealwave – By the Numbers</div></div>
  </div>
  <span class="learn">Learn more</span>
  <div class="section-label">TOP POSTS BY CLICKS</div>
  <div class="top-list">
    <div class="top-item"><div class="t">Comparing Direct Mail to Dealwave – By the Numbers</div><div class="d">March 4, 2013</div></div>
    <div class="top-item"><div class="t">Comparing Direct Mail to Dealwave – By the Numbers</div><div class="d">March 4, 2013</div></div>
    <div class="top-item"><div class="t">Comparing Direct Mail to Dealwave – By the Numbers</div><div class="d">March 4, 2013</div></div>
    <div class="top-item"><div class="t">Comparing Direct Mail to Dealwave – By the Numbers</div><div class="d">March 4, 2013</div></div>
    <div class="top-item"><div class="t">Comparing Direct Mail to Dealwave – By the Numbers</div><div class="d">March 4, 2013</div></div>
    <div class="top-item"><div class="t">Comparing Direct Mail to Dealwave – By the Numbers</div><div class="d">March 4, 2013</div></div>
    <div class="top-item"><div class="t">Comparing Direct Mail to Dealwave – By the Numbers</div><div class="d">March 4, 2013</div></div>
    <div class="top-item"><div class="t">Comparing Direct Mail to Dealwave – By the Numbers</div><div class="d">March 4, 2013</div></div>
  </div>
</aside>

<footer class="footer">
  <div class="f-about"><h4>About Hollow Peak Desk</h4><p>Unhappy with the results of a direct mail small scale campaign, I decided to compare the results to a Dealwave campaign I completed with the cost of the equivalent campaigns. The revenue generated, the customers acquired.</p></div>
  <div class="f-links"><h4>Quick Links</h4><ul><li>Small Business</li><li>Technology</li><li>About Rowan</li><li>Contact</li></ul></div>
  <div><h4>Social Media</h4><p>Connect with us on social channels</p>
    <div class="social"><span><i></i>Social One</span><span><i></i>Social Two</span><span><i></i>Social Three</span><span><i></i>Social Four</span><span><i></i>Social Five</span><span><i></i>Social Six</span></div>
  </div>
</footer>
<div class="copyright">Copyright © 2013, Hollow Peak Desk. All rights reserved.<span class="to-top"></span></div>
</body>
</html>
```